Investor Slide Deck

Simple idea - take a model investor deck and build out a investor deck for K7V. I will complete the data, I need a template to work from within. I will attach a model investor deck and a blank K7V that I need built out to K7V. Use the K7V Pwrpt to build out the investor deck

```html
<!DOCTYPE html>
<html lang="en">
<head>
<meta charset="utf-8">
<title>K7V Investor Deck</title>
<link href="https://fonts.googleapis.com/css2?family=Quicksand:wght@600;700&family=Roboto:wght@400;500;700&display=swap" rel="stylesheet">
<style>
:root{
  --board:#7d7d7d;
  --ink:#0e3440;
  --deep:#0b3440;
  --orange:#ff5a00;
  --coral:#f26a2e;
  --magenta:#b0105a;
  --teal:#14aaa0;
  --green:#6aa83c;
  --yellow:#f7b924;
  --grey:#5a6166;
  --white:#fff;
}
*{margin:0;padding:0;box-sizing:border-box}
html,body{width:989px;height:1200px;overflow:hidden;background:var(--board)}
body{position:relative;font-family:'Roboto',sans-serif;color:var(--ink)}
.slide{position:absolute;width:430px;height:242px;overflow:hidden;background:var(--white)}
.col-l{left:48px}.col-r{left:512px}
.row1{top:58px}.row2{top:339px}.row3{top:619px}.row4{top:900px}
.abs{position:absolute}
.h-title{font-family:'Quicksand',sans-serif;font-weight:700;font-size:13px;color:var(--ink);position:absolute;left:27px;top:8px}
.brand{position:absolute;font-family:'Roboto',sans-serif;font-weight:700;color:var(--ink);white-space:nowrap}
.brand-head{right:27px;top:10px;font-size:5.5px;letter-spacing:.2px}
.foot{position:absolute;left:0;bottom:0;width:100%;height:13px;background:var(--magenta);color:var(--white);font-size:4.6px;display:flex;align-items:center;justify-content:space-between;padding:0 8px 0 27px}
.foot.orange{background:var(--orange)}
.foot .brand{position:static;color:var(--white);font-size:3.8px}
.foot .copy{position:absolute;left:159px}
.photo{position:absolute}
.tiny{font-size:4.4px;line-height:1.5;color:var(--grey)}
.item-t{font-size:7px;font-weight:500;color:var(--ink)}
.card{position:absolute;top:44px;width:112px;height:162px;border-radius:4px;border:2px solid #fff;box-shadow:0 1px 4px rgba(0,0,0,.25);color:#fff;overflow:hidden}
.card .pic{height:69px}
.card h3{font-size:7px;font-weight:500;margin:9px 7px 6px;line-height:1.3}
.card ul{list-style:none;margin:0 7px}
.card li{font-size:4.9px;margin-bottom:3.8px;padding-left:9px;position:relative;line-height:1.4}
.card li:before{content:"";position:absolute;left:0;top:1px;width:4px;height:4px;border-radius:50%;background:#fff}
.dot{position:absolute;border-radius:50%}
.center{text-align:center}
.ms-date{font-size:6.5px;font-weight:500;line-height:1.4}
</style>
</head>
<body>

<!-- Title slide -->
<section class="slide col-l row1" style="background:var(--deep)">
  <div class="photo" role="img" aria-label="Aerial view of wind turbines and a solar farm with dark teal overlay" style="inset:0;background:linear-gradient(180deg,#1f4a55 0%,#123d48 45%,#0d3540 100%)"></div>
  <div class="abs center" style="left:0;width:100%;top:44px;font-family:'Quicksand',sans-serif;font-weight:700;font-size:36px;color:var(--orange)">K7V</div>
  <div class="abs center" style="left:0;width:100%;top:112px;font-family:'Quicksand',sans-serif;font-weight:700;font-size:22px;color:#fff">Presentation Title Goes Here!</div>
  <div class="abs center" style="left:0;width:100%;top:143px;font-size:8.5px;color:#fff">Subtitle of Presentaion Goes Here</div>
  <div class="abs center" style="left:178px;top:169px;width:74px;height:13px;border-radius:7px;background:var(--teal);color:#fff;font-size:5.8px;line-height:13px">Investor Deck, 2024</div>
  <footer class="foot orange"><span class="brand">K7V KESTREL 7 VENTURES</span><span class="copy">© 2024 Kestrel 7 Ventures | All Rights Reserved</span><span>01</span></footer>
</section>

<!-- Problems -->
<section class="slide col-r row1">
  <div class="abs" role="img" aria-label="Faint dotted world map" style="left:40px;top:20px;width:380px;height:210px;background:radial-gradient(ellipse at 60% 50%,#efefef 0%,#fafafa 60%,#fff 100%)"></div>
  <div class="abs" style="left:0;top:0;width:25px;height:242px;background:var(--deep)"></div>
  <div class="abs" style="left:-20px;top:112px;width:66px;transform:rotate(-90deg);font-family:'Quicksand',sans-serif;font-weight:700;font-size:13px;color:#fff;text-align:center">Problems</div>
  <div class="brand brand-head">K7V KESTREL 7 VENTURES</div>
  <svg class="abs" style="left:0;top:0" width="430" height="242" viewBox="0 0 430 242">
    <circle cx="104" cy="120" r="55" fill="none" stroke="#b9b9b9" stroke-width="1" stroke-dasharray="1 2"/>
    <path d="M131 66 Q180 90 190 120 Q180 155 131 174" fill="none" stroke="#888" stroke-width="1" stroke-dasharray="1.5 1.5"/>
    <circle cx="104" cy="120" r="40" fill="#f3f3f3" stroke="#fff" stroke-width="3"/>
    <circle cx="131" cy="67" r="4" fill="#fff" stroke="var(--teal)" stroke-width="1.5"/>
    <circle cx="160" cy="88" r="4" fill="#fff" stroke="var(--magenta)" stroke-width="1.5"/>
    <circle cx="160" cy="153" r="4" fill="#fff" stroke="var(--coral)" stroke-width="1.5"/>
    <circle cx="131" cy="173" r="4" fill="#fff" stroke="var(--yellow)" stroke-width="1.5"/>
    <circle cx="171" cy="120" r="4" fill="#fff" stroke="var(--green)" stroke-width="1.5"/>
    <g stroke-width="3.5" fill="#fff">
      <circle cx="131" cy="39" r="16" stroke="var(--teal)"/>
      <circle cx="173" cy="71" r="16" stroke="var(--magenta)"/>
      <circle cx="190" cy="120" r="16" stroke="var(--green)"/>
      <circle cx="173" cy="170" r="16" stroke="var(--coral)"/>
      <circle cx="131" cy="204" r="16" stroke="var(--yellow)"/>
    </g>
  </svg>
  <div class="abs center" style="left:64px;top:106px;width:80px;font-family:'Quicksand',sans-serif;font-weight:700;font-size:24px;color:var(--orange)">K7V</div>
  <div class="abs" style="left:155px;top:18px;width:200px"><div class="item-t">Poor Quality Components</div><div class="tiny">The use of low-quality solar panels and components in solar plant construction is impacting their efficiency and lifespan.</div></div>
  <div class="abs" style="left:197px;top:55px;width:205px"><div class="item-t">Poor Installation</div><div class="tiny">Solar plant installations demand precision; poor installation can lead to downtime, damage, and efficiency loss.</div></div>
  <div class="abs" style="left:213px;top:109px;width:195px"><div class="item-t">Lack of Awareness</div><div class="tiny">Limited awareness of government subsidies and inadequate financing options for high-cost solar plant purchases can lead to missed product benefits</div></div>
  <div class="abs" style="left:197px;top:159px;width:200px"><div class="item-t">Unreliable Customer and Warranty Support</div><div class="tiny">Challenges in reaching timely support and clarifying warranty terms can result in customer frustration and self-reliance for issue resolution</div></div>
  <div class="abs" style="left:155px;top:199px;width:220px"><div class="item-t">Lack of Transparency in Pricing and Performance</div><div class="tiny">Customers might encounter unexpected hidden costs during installation and lower energy generation than initially agreed upon.</div></div>
</section>

<!-- Services cards -->
<section class="slide col-l row2">
  <h2 class="h-title">Our Services</h2>
  <div class="brand brand-head">K7V KESTREL 7 VENTURES</div>
  <div class="card" style="left:28px;background:var(--orange)">
    <div class="pic" role="img" aria-label="Solar panels on a house roof" style="background:linear-gradient(160deg,#2b4a7e,#8a4a3a 60%,#d9d9d9)"></div>
    <h3>Solar Power for Homes</h3>
    <ul><li>Electricity Bill to go to Zero</li><li>Low Maintenance Cost</li><li>Assured Warranty upto 25 Years</li><li>Government Subsidies</li></ul>
  </div>
  <div class="card" style="left:159px;background:var(--magenta)">
    <div class="pic" role="img" aria-label="Solar panels on a commercial building roof" style="background:linear-gradient(160deg,#8fa6b8,#3d5f86 55%,#c7cdd2)"></div>
    <h3>Solar Power for Business</h3>
    <ul><li>Clean Energy</li><li>Tax Benefits</li><li>Grid Tied Systems</li><li>Finance Support</li></ul>
  </div>
  <div class="card" style="left:290px;background:var(--teal)">
    <div class="pic" role="img" aria-label="Utility scale solar power plant field" style="background:linear-gradient(170deg,#9db79a,#5c7896 50%,#c0ccd3)"></div>
    <h3>Utility Scale Solar Power Plant</h3>
    <ul><li>Generate and Sell electricity to the government and industrial plants</li><li>Long term stable prices for generated electricity from solar power plant</li></ul>
  </div>
  <footer class="foot"><span class="brand">K7V KESTREL 7 VENTURES</span><span class="copy">© 2024 Kestrel 7 Ventures | All Rights Reserved</span><span>03</span></footer>
</section>

<!-- Services list -->
<section class="slide col-r row2">
  <svg class="abs" style="left:0;top:0" width="160" height="242" viewBox="0 0 160 242">
    <defs><linearGradient id="eng" x1="0" y1="0" x2="1" y2="1"><stop offset="0" stop-color="#a9cbe3"/><stop offset=".55" stop-color="#c9c24a"/><stop offset="1" stop-color="#5f7a3a"/></linearGradient></defs>
    <circle cx="24" cy="111" r="118" fill="none" stroke="var(--deep)" stroke-width="5"/>
    <circle cx="24" cy="111" r="115" fill="url(#eng)" role="img" aria-label="Two engineers in hard hats reviewing plans at a solar site"/>
    <path d="M152 130 A130 130 0 0 1 110 203" fill="none" stroke="var(--teal)" stroke-width="5" stroke-linecap="round"/>
  </svg>
  <h2 class="h-title" style="left:170px">Our Services</h2>
  <div class="brand brand-head">K7V KESTREL 7 VENTURES</div>
  <div class="dot" style="left:170px;top:46px;width:32px;height:32px;background:var(--orange)"></div>
  <div class="dot" style="left:170px;top:93px;width:32px;height:32px;background:var(--teal)"></div>
  <div class="dot" style="left:170px;top:138px;width:32px;height:32px;background:var(--magenta)"></div>
  <div class="dot" style="left:170px;top:181px;width:32px;height:32px;background:var(--yellow)"></div>
  <div class="abs" style="left:210px;top:44px;width:200px"><div class="item-t">EPC Solutions</div><div class="tiny">Get turnkey EPC solutions that cover engineering, procurement, and construction. We develop long-term solutions that have a direct impact on the environment. Take care of all your electricity requirements.</div></div>
  <div class="abs" style="left:210px;top:90px;width:200px"><div class="item-t">Installation and Commission</div><div class="tiny">With our 24/7 remote monitoring, you may install and run solar panels without worrying about performance issues. We offer complete solutions. We provide support for all the systems we install for you.</div></div>
  <div class="abs" style="left:210px;top:140px;width:200px"><div class="item-t">Solar Financing</div><div class="tiny">With our assistance, you can finance the installation of solar panels and renewable energy. We locate the best source for you to apply for and obtain the best solar loans.</div></div>
  <div class="abs" style="left:210px;top:182px;width:200px"><div class="item-t">Operation and Maintenance</div><div class="tiny">Get expert advice on how to run the solar plant once it has been installed. To care for your system and maintain its proper operation, we adhere to all applicable rules.</div></div>
  <footer class="foot"><span class="brand">K7V KESTREL 7 VENTURES</span><span class="copy">© 2024 Kestrel 7 Ventures | All Rights Reserved</span><span>04</span></footer>
</section>

<!-- Competitive advantage -->
<section class="slide col-l row3">
  <h2 class="h-title">Competitive Advantage</h2>
  <div class="brand brand-head">K7V KESTREL 7 VENTURES</div>
  <svg class="abs" style="left:0;top:0" width="430" height="242" viewBox="0 0 430 242">
    <defs><linearGradient id="sky" x1="0" y1="0" x2="0" y2="1"><stop offset="0" stop-color="#7fa3d6"/><stop offset=".6" stop-color="#dfe6ee"/><stop offset="1" stop-color="#3c5a8c"/></linearGradient></defs>
    <circle cx="211" cy="111" r="70" fill="url(#sky)" role="img" aria-label="Sky with clouds over solar panels"/>
    <circle cx="212" cy="79" r="36" fill="var(--magenta)"/>
    <path d="M247 92 A38 38 0 0 1 220 119" fill="none" stroke="var(--magenta)" stroke-width="2"/>
    <circle cx="165" cy="161" r="33" fill="var(--green)"/>
    <path d="M195 179 A36 36 0 0 1 172 198" fill="none" stroke="var(--green)" stroke-width="2"/>
    <circle cx="252" cy="161" r="33" fill="var(--coral)"/>
    <path d="M282 179 A36 36 0 0 1 259 198" fill="none" stroke="var(--coral)" stroke-width="2"/>
    <g fill="none" stroke="#fff" stroke-width="1.5"><circle cx="212" cy="75" r="9"/><path d="M208 75l3 3 5-6M198 93l8 4h12l9-6"/><circle cx="165" cy="161" r="10"/><path d="M160 161l4 4 7-8"/><circle cx="252" cy="158" r="9"/><path d="M248 170h8"/></g>
  </svg>
  <div class="abs" style="left:252px;top:56px;width:125px"><div class="item-t" style="font-size:8px">Focus on Quality</div><div class="tiny">Our stringent quality control methods enable us to provide high-quality products that we provide warranties upto 25 years</div></div>
  <div class="abs" style="left:27px;top:141px;width:95px;text-align:right"><div class="item-t" style="font-size:8px;white-space:nowrap">Unrivalled Experience</div><div class="tiny">We have worked on 2500+ projects with a diverse client base while maintaining consistent quality. Experience and Technology enable us to provide best results for our customers.</div></div>
  <div class="abs" style="left:295px;top:144px;width:115px"><div class="item-t" style="font-size:8px">State of the Art Technology</div><div class="tiny">Our access to advanced technology lets us create cutting-edge solar solutions that adapt flexibly to suit specific requirements.</div></div>
  <footer class="foot"><span class="brand">K7V KESTREL 7 VENTURES</span><span class="copy">© 2024 Kestrel 7 Ventures | All Rights Reserved</span><span>05</span></footer>
</section>

<!-- Market opportunity -->
<section class="slide col-r row3">
  <div class="abs" style="left:0;top:0;width:140px;height:242px;background:var(--deep)"></div>
  <div class="abs center" style="left:0;top:20px;width:140px;color:#fff;font-family:'Quicksand',sans-serif;font-weight:700;font-size:10px">Indian Solar Energy</div>
  <div class="abs center" style="left:0;top:35px;width:140px;color:#fff;font-size:6px;font-weight:500">Market Size</div>
  <svg class="abs" style="left:0;top:0" width="430" height="242" viewBox="0 0 430 242">
    <polygon points="21,137 35,130 51,137 51,206 35,212 21,206" fill="#f7c12a"/>
    <polygon points="21,137 35,130 51,137 37,143" fill="#ffe35a"/>
    <polygon points="37,143 51,137 51,206 37,212" fill="#f29b12"/>
    <polygon points="80,88 98,81 119,88 119,206 98,212 80,206" fill="#f7c12a"/>
    <polygon points="80,88 98,81 119,88 100,94" fill="#ffe35a"/>
    <polygon points="100,94 119,88 119,206 100,212" fill="#f29b12"/>
    <circle cx="227" cy="124" r="72" fill="var(--green)"/>
    <circle cx="227" cy="147" r="55" fill="var(--magenta)"/>
    <circle cx="227" cy="162" r="39" fill="var(--teal)"/>
    <g stroke-width=".6" stroke-dasharray="1 1"><line x1="240" y1="59" x2="310" y2="59" stroke="var(--green)"/><line x1="262" y1="108" x2="310" y2="108" stroke="var(--magenta)"/><line x1="255" y1="155" x2="310" y2="155" stroke="var(--teal)"/></g>
    <g><circle cx="310" cy="59" r="1.2" fill="var(--green)"/><circle cx="310" cy="108" r="1.2" fill="var(--magenta)"/><circle cx="310" cy="155" r="1.2" fill="var(--teal)"/></g>
  </svg>
  <div class="abs" style="left:27px;top:195px;transform:rotate(-90deg);font-size:4.5px;color:#8a5a00">2022</div>
  <div class="abs" style="left:86px;top:140px;transform:rotate(-90deg);font-size:4.5px;color:#8a5a00">2032</div>
  <div class="abs" style="left:27px;top:113px;color:#fff;font-size:7px;font-weight:500">$38B</div>
  <div class="abs" style="left:88px;top:71px;color:#fff;font-size:7px;font-weight:500">$238B</div>
  <h2 class="h-title" style="left:165px">Market Opportunity</h2>
  <div class="brand brand-head">K7V KESTREL 7 VENTURES</div>
  <div class="abs center" style="left:187px;top:59px;width:80px;color:#fff"><div style="font-size:10px;font-weight:700">$234.86B</div><div style="font-size:5px">TAM</div></div>
  <div class="abs center" style="left:187px;top:93px;width:80px;color:#fff"><div style="font-size:10px;font-weight:700">$38B</div><div style="font-size:5px">SAM</div></div>
  <div class="abs center" style="left:187px;top:147px;width:80px;color:#fff"><div style="font-size:10px;font-weight:700">$116M</div><div style="font-size:5px">SOM</div></div>
  <div class="abs" style="left:324px;top:55px;width:90px"><div style="font-size:6px;font-weight:500;color:var(--green)">Total Addressable Market</div><div class="tiny">The Global Solar Energy Market was valued at $234.86B in 2022 Source: Northfield Insights</div></div>
  <div class="abs" style="left:324px;top:104px;width:90px"><div style="font-size:6px;font-weight:500;color:var(--magenta);white-space:nowrap">Serviceable Available Market</div><div class="tiny">The Indian Solar Energy Market was valued at $38B in 2022. Source: Meridian Research</div></div>
  <div class="abs" style="left:324px;top:151px;width:78px"><div style="font-size:6px;font-weight:500;color:var(--teal)">Serviceable Obtainable Market</div><div class="tiny">Company Name Energy aims to generate $ 116 Mn of revenues in the third year of its plant operations</div></div>
  <footer class="foot"><span class="brand">K7V KESTREL 7 VENTURES</span><span class="copy">© 2024 Kestrel 7 Ventures | All Rights Reserved</span><span>07</span></footer>
</section>

<!-- Milestones -->
<section class="slide col-l row4">
  <h2 class="h-title">Milestones</h2>
  <div class="brand brand-head">K7V KESTREL 7 VENTURES</div>
  <svg class="abs" style="left:0;top:0" width="430" height="242" viewBox="0 0 430 242">
    <g stroke-width="5" fill="#fff">
      <path d="M62 138 L70 153 L78 138" fill="var(--teal)"/><circle cx="70" cy="120" r="21" stroke="var(--teal)"/>
      <path d="M134 110 L142 95 L150 110" fill="var(--magenta)"/><circle cx="142" cy="128" r="21" stroke="var(--magenta)"/>
      <path d="M206 138 L214 153 L222 138" fill="var(--green)"/><circle cx="214" cy="120" r="21" stroke="var(--green)"/>
      <path d="M279 110 L287 95 L295 110" fill="var(--coral)"/><circle cx="287" cy="128" r="21" stroke="var(--coral)"/>
      <path d="M351 138 L359 153 L367 138" fill="var(--yellow)"/><circle cx="359" cy="120" r="21" stroke="var(--yellow)"/>
    </g>
  </svg>
  <div class="abs center ms-date" style="left:30px;top:156px;width:80px">September<br>2019</div>
  <div class="abs center tiny" style="left:35px;top:183px;width:70px">First Tender Bid for Aruna Location Solar under Govt. Subsidy Scheme.</div>
  <div class="abs center tiny" style="left:107px;top:46px;width:70px">Served over 1000 customers with over 3.5Mw of Solar Installation.</div>
  <div class="abs center ms-date" style="left:102px;top:77px;width:80px">December<br>2021</div>
  <div class="abs center ms-date" style="left:174px;top:156px;width:80px">August<br>2023</div>
  <div class="abs center tiny" style="left:179px;top:183px;width:70px">Served over 2500 Customers with over 8MW of Solar Installation.</div>
  <div class="abs center tiny" style="left:252px;top:46px;width:70px">Opening our Branch Office in the city of Indore, Madhya Pradesh, India.</div>
  <div class="abs center ms-date" style="left:247px;top:77px;width:80px">August<br>2023</div>
  <div class="abs center ms-date" style="left:319px;top:156px;width:80px">August<br>2023</div>
  <div class="abs center tiny" style="left:322px;top:183px;width:74px">Introducing Solar Panels and Inverters under Company Name Brand</div>
  <footer class="foot"><span class="brand">K7V KESTREL 7 VENTURES</span><span class="copy">© 2024 Kestrel 7 Ventures | All Rights Reserved</span><span>07</span></footer>
</section>

<!-- Thank you -->
<section class="slide col-r row4">
  <div class="abs" style="left:230px;top:0;width:200px;height:242px;background:var(--deep)"></div>
  <div class="brand" style="left:27px;top:26px;font-size:9px">K7V KESTREL 7 VENTURES</div>
  <div class="abs" style="left:27px;top:118px;font-family:'Quicksand',sans-serif;font-weight:700;font-size:22px;color:var(--ink)">THANK YOU</div>
  <svg class="abs" style="left:0;top:0" width="430" height="242" viewBox="0 0 430 242">
    <circle cx="230" cy="53" r="20" fill="var(--orange)"/>
    <path d="M223 44c2-2 4-1 5 1l1 3c0 1-1 2-2 3 1 3 3 5 6 6 1-1 2-2 3-2l3 1c2 1 3 3 1 5-3 3-9 1-13-3s-6-10-4-14z" fill="#fff"/>
    <circle cx="230" cy="121" r="20" fill="var(--yellow)"/>
    <g fill="none" stroke="#fff" stroke-width="1.4"><circle cx="230" cy="121" r="9"/><ellipse cx="230" cy="121" rx="4" ry="9"/><line x1="221" y1="121" x2="239" y2="121"/><path d="M222 116h16M222 126h16"/></g>
    <circle cx="230" cy="189" r="20" fill="var(--teal)"/>
    <g fill="none" stroke="#fff" stroke-width="1.4"><rect x="220" y="182" width="20" height="14" rx="1"/><path d="M220 182l10 8 10-8M220 196l7-6M240 196l-7-6"/></g>
  </svg>
  <div class="abs" style="left:262px;top:40px;color:#fff"><div style="font-size:6.5px">Phone Number</div><div style="font-size:9px;font-weight:500;margin-top:4px">555.010.7788</div></div>
  <div class="abs" style="left:262px;top:108px;color:#fff"><div style="font-size:6.5px">Website</div><div style="font-size:9px;font-weight:500;margin-top:4px">www.kestrel7ventures.com</div></div>
  <div class="abs" style="left:262px;top:176px;color:#fff"><div style="font-size:6.5px">E-mail Address</div><div style="font-size:9px;font-weight:500;margin-top:4px">info@kestrel7ventures.com</div></div>
</section>

</body>
</html>
```